Professional violinist needs business cards

I am trying to attract the following jobs:
-private violin lessons (primarily classical)
-performance gigs (weddings, birthday parties, funerals, etc.)
-collaborations with other artists (studio recordings, performances)

I want to communicate that I have a very high standard of excellence for my work, but I also love people and celebrations.
Values/style words I like are:
love, joy, peace, fun, beauty, authenticity, excellence, warmth, refined/sleek, free spirited. If that's too confusing, just ignore :)

I will attach my favorite business card template that I could find on Canva. The lines are supposed to be like a music staff, which I think is really cool, but I also don't want it to look too busy. I like the simple black and white--I think it looks sharp--but I also am open to other ideas. I also have seen business cards with pictures included that looked great, so I attached an image that could be used as well.

I am also attaching a file that I made of my initials that could be used as a logo, but I'm not sure if it should be included.

Information on the card:
-My name (18 letters total)
-"violinist"
-phone number, email, website

Thank you!

```html
<!DOCTYPE html>
<html lang="en">
<head>
<meta charset="utf-8">
<title>Juliette Harwood – Violinist Business Cards</title>
<link href="https://fonts.googleapis.com/css2?family=Dancing+Script:wght@500&family=Cinzel:wght@500&family=Crimson+Text&display=swap" rel="stylesheet">
<style>
  :root {
    --backdrop: #2b2b2c;
    --card-ink: #1f2327;
    --gold: #c8b591;
    --ivory: #ece8e1;
    --silver: #d9dadc;
    --stone: #262727;
    --stone-light: #363738;
  }
  * { margin: 0; padding: 0; box-sizing: border-box; }
  html, body { width: 1200px; height: 1138px; overflow: hidden; }
  body { background: var(--backdrop); position: relative; }

  .card {
    position: absolute;
    width: 620px;
    height: 374px;
    border-radius: 16px;
    overflow: hidden;
    background: var(--card-ink);
  }
  .card--front { left: 274px; top: 186px; }
  .card--back {
    left: 276px; top: 608px;
    background: linear-gradient(135deg, var(--stone-light), var(--stone) 60%, #1e1f1f);
  }

  .clef-decoration {
    position: absolute; left: 0; top: 0;
    width: 142px; height: 100%;
    background: linear-gradient(90deg, rgba(217,218,220,0.22), rgba(217,218,220,0.08));
  }
  .portrait-photo {
    position: absolute; left: 0; top: 0;
    width: 224px; height: 100%;
    background: linear-gradient(180deg, #141414 0%, #1a1412 40%, #4a2a16 65%, #1a1210 100%);
  }

  .identity {
    position: absolute;
    transform: translateX(-50%);
    text-align: center;
  }
  .card--front .identity { left: 376px; top: 74px; }
  .card--back .identity { left: 426px; top: 54px; }

  .brand-mark {
    display: flex;
    align-items: flex-end;
    justify-content: center;
    font-family: "Crimson Text", serif;
    font-weight: 400;
    color: var(--gold);
    white-space: nowrap;
    line-height: 1;
  }
  .card--front .brand-mark { font-size: 22px; height: 112px; padding-bottom: 18px; }
  .card--back .brand-mark { font-size: 18px; height: 80px; padding-bottom: 12px; }

  .name {
    font-family: "Dancing Script", cursive;
    font-weight: 500;
    color: var(--ivory);
    white-space: nowrap;
    line-height: 1.1;
  }
  .card--front .name { font-size: 40px; margin-top: 12px; }
  .card--back .name { font-size: 36px; margin-top: 4px; }

  .title-row {
    display: flex; align-items: center; justify-content: center;
    gap: 18px; margin-top: 6px;
  }
  .title-row .rule { height: 1px; background: var(--gold); width: 82px; }
  .title {
    font-family: "Cinzel", serif;
    font-weight: 500;
    color: var(--ivory);
    letter-spacing: 3px;
    font-size: 18px;
  }
  .card--back .title-row .rule { width: 68px; }
  .card--back .title { font-size: 16px; }

  .contact {
    list-style: none;
    margin-top: 26px;
    font-family: "Crimson Text", serif;
    font-size: 16px;
    line-height: 23px;
    color: var(--ivory);
  }
  .contact .accent { color: var(--gold); }
</style>
</head>
<body>
  <section class="card card--front">
    <div class="clef-decoration" role="img" aria-label="Large silver treble clef along the left edge"></div>
    <div class="identity">
      <div class="brand-mark">Juliette Harwood</div>
      <div class="name">Juliette Harwood</div>
      <div class="title-row"><span class="rule"></span><span class="title">Violinist</span><span class="rule"></span></div>
    </div>
  </section>

  <section class="card card--back">
    <div class="portrait-photo" role="img" aria-label="Photo of a violinist in a black dress holding a violin and bow"></div>
    <div class="identity">
      <div class="brand-mark">Juliette Harwood</div>
      <div class="name">Juliette Harwood</div>
      <div class="title-row"><span class="rule"></span><span class="title">Violinist</span><span class="rule"></span></div>
      <ul class="contact">
        <li>+1 (555) 014-2280</li>
        <li>Juliette@JulietteHarwood.com</li>
        <li>www.<span class="accent">JulietteHarwood</span>.com</li>
        <li>Annapolis, MD</li>
      </ul>
    </div>
  </section>
</body>
</html>
```